Kellwyn Surface Records

I have a current web site that it looking quite aged and it needs a new lease of life. This is a Graffiti Management Website so is all about data processing and management of information. I want a html 5 view on any platform design. clean crisp and new. I have provided some screen shots of my current site.

Target Market(s)

The Target Market will be local government. most users will not be heavy pc users

Industry/Entity Type

Management

Font styles to use
Sans Serif
Other font styles liked:
• web font like calibri

Colors

Designer to choose colors to be used in the design.

Requirements
Must have
• Must have menus similar to attachments

```html
<!DOCTYPE html>
<html lang="en">
<head>
<meta charset="utf-8">
<title>KSR – Kellwyn Surface Records</title>
<link rel="stylesheet" href="https://fonts.googleapis.com/css2?family=Open+Sans:wght@400;600;700;800&display=swap">
<style>
:root{
  --orange:#e9a11b;
  --orange-dark:#c9860e;
  --orange-soft:#f5c865;
  --ink:#2b2b2b;
  --night:#1f1f1f;
  --grey:#ededed;
  --text:#444;
  --white:#fff;
}
*{box-sizing:border-box;margin:0;padding:0}
html,body{width:710px;height:1200px;overflow:hidden;background:var(--white)}
body{font-family:"Open Sans",Arial,sans-serif;color:var(--text);position:relative}

/* navigation */
.site-nav{position:absolute;top:0;left:0;width:710px;height:52px;background:rgba(20,20,20,.92);z-index:3;display:flex;justify-content:center;gap:4px;padding-top:14px}
.site-nav a{color:var(--white);font-size:12px;font-weight:700;text-decoration:none;padding:6px 14px;height:24px;letter-spacing:.3px}
.site-nav a.active{background:var(--orange)}

/* hero */
.hero{position:absolute;top:0;left:0;width:710px;height:355px;background:linear-gradient(135deg,#5b4a3a 0%,#3d3f46 35%,#6a5236 60%,#2f3338 100%)}
.hero-shade{position:absolute;inset:0;background:rgba(0,0,0,.45)}
.brand{position:absolute;top:112px;left:0;width:710px;display:flex;justify-content:center;align-items:center;gap:10px;color:var(--white);font-size:24px;font-weight:700;line-height:30px}
.brand-mark{width:14px;height:14px;background:var(--orange)}
.hero-title{position:absolute;top:246px;width:710px;text-align:center;color:var(--white);font-size:19px;font-weight:600;line-height:22px}
.hero-note{position:absolute;top:292px;width:710px;text-align:center;color:var(--white);font-size:9px;letter-spacing:.4px}
.hero-dots{position:absolute;top:314px;left:340px;display:flex;gap:6px}
.hero-dots span{width:7px;height:7px;border-radius:50%;background:#aaa}
.hero-dots span.on{background:var(--white)}

/* about */
.section-title{font-size:22px;font-weight:700;color:var(--ink);text-align:center}
.about{position:absolute;top:355px;left:0;width:710px;height:320px;background:var(--white)}
.about .section-title{position:absolute;top:20px;width:710px}
.about-text{position:absolute;top:72px;left:42px;width:400px;font-size:9px;line-height:14px}
.about-text strong{display:block;font-size:11.5px;color:var(--ink);margin-bottom:12px}
.about-text p{margin-bottom:10px}
.benefits{position:absolute;top:205px;left:36px;display:flex;gap:22px}
.benefit{width:82px;text-align:center;font-size:9px;color:var(--ink);line-height:11px}
.benefit svg{display:block;margin:0 auto 6px;width:32px;height:32px}
.benefit.first{border-bottom:3px solid var(--orange);padding-bottom:4px}

.report-card{position:absolute;top:52px;left:473px;width:213px;height:260px;background:var(--orange);color:var(--white);padding:14px 18px;z-index:2;box-shadow:0 2px 6px rgba(0,0,0,.15)}
.report-card p{font-size:9px;line-height:12px;font-weight:600}
.report-card p b{color:var(--ink)}
.report-chart{margin-top:12px;width:177px;height:118px;display:block}
.btn{display:inline-block;background:var(--night);color:var(--white);font-size:8px;font-weight:700;padding:5px 10px;text-transform:uppercase;letter-spacing:.4px}
.report-card .btn{position:absolute;bottom:20px;left:73px}

/* products */
.products{position:absolute;top:675px;left:0;width:710px;height:253px;background:var(--grey)}
.products .section-title{position:absolute;top:22px;width:710px}
.product-list{position:absolute;top:70px;left:52px;display:flex;gap:8px}
.product{width:201px;height:131px;background:var(--orange);color:var(--white);padding:14px 14px 0;position:relative}
.product h3{font-size:11px;font-weight:700;display:flex;align-items:center;gap:8px;padding-bottom:6px;border-bottom:1px solid rgba(255,255,255,.6);margin-bottom:7px}
.product p{font-size:8.5px;line-height:11px;text-align:center}
.product .btn{position:absolute;bottom:12px;left:78px}
.slider-arrow{position:absolute;top:128px;width:12px;height:22px}
.slider-arrow.prev{left:14px}.slider-arrow.next{right:14px}

/* legislation */
.legislation{position:absolute;top:928px;left:0;width:710px;height:125px;background:linear-gradient(90deg,#242424,#3a3a3a 50%,#242424)}
.legislation h2{color:var(--white);text-align:center;font-size:20px;font-weight:700;margin-top:16px}
.legislation p{color:var(--white);text-align:center;font-size:10.5px;line-height:22px;width:560px;margin:8px auto 0}

/* footer */
.site-footer{position:absolute;top:1053px;left:0;width:710px;height:147px;background:var(--white);font-size:8.5px;color:var(--ink)}
.copyright{position:absolute;top:86px;left:22px;color:var(--orange-dark);font-weight:600}
.footer-brand{position:absolute;top:14px;left:292px;display:flex;gap:8px;line-height:12px}
.footer-brand .mark{width:12px;height:12px;background:var(--orange);margin-top:2px}
.footer-contact{position:absolute;top:14px;left:555px;line-height:12px}
.social{position:absolute;top:112px;left:277px;display:flex;gap:18px}
.social span{width:16px;height:16px;border-radius:50%;background:var(--night)}
.footer-line{position:absolute;bottom:0;left:0;width:710px;height:4px;background:var(--orange)}
</style>
</head>
<body>

<div class="hero" role="img" aria-label="Photograph of a wall covered in colourful graffiti">
  <div class="hero-shade"></div>
</div>

<nav class="site-nav">
  <a class="active">HOME</a><a>PRODUCTS</a><a>REPORTS</a><a>BENEFITS</a><a>LEGISLATION</a><a>CONTACT US</a><a>LOG IN</a>
</nav>

<header class="brand">
  <span class="brand-mark"></span>
  <span class="brand-name">Kellwyn Surface Records</span>
</header>
<h1 class="hero-title">HELPING YOU CLEAN UP<br>YOUR COMMUNITY</h1>
<div class="hero-note">OUR WORK IS DEDICATED TO THE PROSPERITY OF YOUR PROPERTIES</div>
<div class="hero-dots"><span></span><span class="on"></span><span></span></div>

<section class="about">
  <h2 class="section-title">About Us</h2>
  <div class="about-text">
    <strong>KSR is an Online Database System to Manage Graffiti in your Area or Your Properties</strong>
    <p>KSR allows you to Register, Track, Report and Archive Graffiti Jobs with Photographic Records. KSR records both Estimated and Actual hours and costs for each job, enabling you to track the effectiveness of Anti Graffiti policy. KSR allows sharing of Critical Graffiti Tag and Photographic Data between its subscribers, assisting with tracking down Serial Graffiti Offenders.</p>
  </div>
  <div class="benefits">
    <div class="benefit first">
      <svg viewBox="0 0 32 32"><path d="M4 16 L16 4 H28 V16 L16 28 Z" fill="none" stroke="var(--orange)" stroke-width="2.5"/><circle cx="22" cy="10" r="2.5" fill="var(--orange)"/></svg>Cost<br>Effective
    </div>
    <div class="benefit">
      <svg viewBox="0 0 32 32"><rect x="3" y="9" width="26" height="18" rx="2" fill="var(--orange)"/><rect x="11" y="5" width="10" height="5" fill="var(--orange)"/><circle cx="16" cy="18" r="5.5" fill="#fff"/><circle cx="16" cy="18" r="3" fill="var(--orange)"/></svg>Photographic<br>Records
    </div>
    <div class="benefit">
      <svg viewBox="0 0 32 32"><path d="M10 14 V10 a6 6 0 0 1 12 0 V14" fill="none" stroke="var(--orange)" stroke-width="3"/><rect x="6" y="14" width="20" height="15" rx="2" fill="var(--orange)"/><circle cx="16" cy="21" r="2.5" fill="#fff"/></svg>Access &amp;<br>Security
    </div>
    <div class="benefit">
      <svg viewBox="0 0 32 32"><rect x="8" y="5" width="16" height="8" rx="1" transform="rotate(-35 16 9)" fill="var(--orange)"/><rect x="15" y="12" width="4" height="14" transform="rotate(-35 17 19)" fill="var(--orange)"/><rect x="5" y="27" width="18" height="3" fill="var(--orange)"/></svg>Assist<br>Prosecution
    </div>
  </div>

  <aside class="report-card">
    <p><b>KSR</b> has <b>Statistical and Comparison Reporting System</b> to allow its subscribers to <b>graphically report</b> and compare their <b>Graffiti Data</b></p>
    <svg class="report-chart" viewBox="0 0 177 118">
      <rect width="177" height="118" fill="#fff"/>
      <g stroke="#eee" stroke-width="1">
        <line x1="22" y1="20" x2="170" y2="20"/><line x1="22" y1="44" x2="170" y2="44"/><line x1="22" y1="68" x2="170" y2="68"/><line x1="22" y1="92" x2="170" y2="92"/>
      </g>
      <line x1="22" y1="10" x2="22" y2="104" stroke="#bbb"/><line x1="22" y1="104" x2="170" y2="104" stroke="#bbb"/>
      <g fill="var(--orange-soft)" stroke="var(--orange)" stroke-width="1">
        <rect x="36" y="60" width="16" height="44"/><rect x="62" y="38" width="16" height="66"/><rect x="88" y="18" width="16" height="86"/><rect x="114" y="50" width="16" height="54"/><rect x="140" y="76" width="16" height="28"/>
      </g>
      <g font-size="6" fill="#999" font-family="Open Sans,sans-serif"><text x="6" y="22">40</text><text x="6" y="46">30</text><text x="6" y="70">20</text><text x="6" y="94">10</text></g>
    </svg>
    <span class="btn">View Reports</span>
  </aside>
</section>

<section class="products">
  <h2 class="section-title">Products</h2>
  <svg class="slider-arrow prev" viewBox="0 0 12 22"><path d="M10 2 L2 11 L10 20" fill="none" stroke="#555" stroke-width="2"/></svg>
  <svg class="slider-arrow next" viewBox="0 0 12 22"><path d="M2 2 L10 11 L2 20" fill="none" stroke="#555" stroke-width="2"/></svg>
  <div class="product-list">
    <article class="product">
      <h3><svg width="16" height="16" viewBox="0 0 16 16"><rect x="2" y="1" width="12" height="14" fill="none" stroke="#fff" stroke-width="1.5"/><line x1="5" y1="5" x2="11" y2="5" stroke="#fff"/><line x1="5" y1="8" x2="11" y2="8" stroke="#fff"/><line x1="5" y1="11" x2="11" y2="11" stroke="#fff"/></svg>GRAFFITI REGISTER</h3>
      <p>KSR provides a Register of incidents and Graffiti jobs.</p>
      <span class="btn">More</span>
    </article>
    <article class="product">
      <h3><svg width="16" height="16" viewBox="0 0 16 16"><rect x="1" y="4" width="14" height="10" rx="1" fill="#fff"/><circle cx="8" cy="9" r="3" fill="var(--orange)"/></svg>GRAFFITI PHOTOS</h3>
      <p>KSR allows its subscribers to add Digital Photographs to the Graffiti Jobs.</p>
      <span class="btn">More</span>
    </article>
    <article class="product">
      <h3><svg width="16" height="16" viewBox="0 0 16 16"><ellipse cx="8" cy="3.5" rx="6" ry="2.5" fill="#fff"/><rect x="2" y="3.5" width="12" height="9" fill="#fff"/><ellipse cx="8" cy="12.5" rx="6" ry="2.5" fill="#fff"/></svg>SEARCHABLE DATABASE</h3>
      <p>KSR allows you to search your own records &amp; limited data from other subscribers.</p>
      <span class="btn">More</span>
    </article>
  </div>
</section>

<section class="legislation">
  <h2>Legislation</h2>
  <p>KSR can assist with the possible prosecution of offenders with records of previous tags made your local area as well as any other subscribers tags. This will effectively show the extent of the offenders activities.</p>
</section>

<footer class="site-footer">
  <div class="copyright">copyright 2014 KSR all rights reserved</div>
  <div class="footer-brand">
    <span class="mark"></span>
    <div>Kellwyn Surface Records<br>PO Box 318 Brayford NSW 2291<br>Ph (02) 9411 2870</div>
  </div>
  <div class="footer-contact">Mail: enquiries@kellwynrecords.com<br>support@kellwynrecords.com</div>
  <div class="social"><span></span><span></span><span></span><span></span><span></span></div>
  <div class="footer-line"></div>
</footer>

</body>
</html>
```